dsadasdasdasdsa

Industry/Entity Type

Mortgage Broking

Requirements
Must have
• Call-to-action button somewhere on the graphic
Nice to have
• The font of our logo is Montserrat

```html
<!DOCTYPE html>
<html lang="en">
<head>
<meta charset="utf-8">
<title>Mortgage Broker Directory Banner</title>
<link href="https://fonts.googleapis.com/css2?family=Montserrat:wght@500;800;900&display=swap" rel="stylesheet">
<style>
  :root {
    --green-deep: #073a22;
    --green-mid: #0f5e33;
    --green-glow: #2fa34e;
    --white: #ffffff;
    --yellow: #f4ee1a;
    --red-top: #c8321f;
    --red-bottom: #8e1d10;
    --cream: #fbe8b4;
    --shell-brown: #8a5a2b;
    --skin-green: #5fb548;
  }
  * { margin: 0; padding: 0; box-sizing: border-box; }
  html, body { width: 1200px; height: 180px; overflow: hidden; }
  body { font-family: "Montserrat", Arial, sans-serif; }

  .banner {
    position: relative;
    width: 1200px;
    height: 180px;
    overflow: hidden;
    background:
      radial-gradient(ellipse 420px 260px at 1040px 90px, rgba(80, 200, 100, 0.55), transparent 70%),
      radial-gradient(ellipse 700px 300px at 520px 90px, var(--green-mid), transparent 80%),
      var(--green-deep);
  }
  .banner__rays {
    position: absolute;
    inset: 0;
    background: repeating-conic-gradient(from 0deg at 1040px 90px,
      rgba(255,255,255,0.06) 0deg 4deg, transparent 4deg 10deg);
    -webkit-mask-image: radial-gradient(ellipse 520px 300px at 1040px 90px, #000 20%, transparent 80%);
            mask-image: radial-gradient(ellipse 520px 300px at 1040px 90px, #000 20%, transparent 80%);
  }

  .headline {
    position: absolute;
    left: 0;
    width: 1040px;
    top: 24px;
    text-align: center;
    color: var(--white);
    font-weight: 500;
    font-size: 38px;
    letter-spacing: 0.5px;
    line-height: 1;
  }
  .subline {
    position: absolute;
    left: 0;
    width: 1040px;
    top: 74px;
    text-align: center;
    color: var(--yellow);
    font-weight: 900;
    font-size: 31px;
    line-height: 1;
  }

  .cta {
    position: absolute;
    left: 168px;
    top: 134px;
    width: 716px;
    height: 70px;
    border-radius: 35px;
    background: linear-gradient(var(--red-top), var(--red-bottom));
    box-shadow: 0 -2px 8px rgba(0,0,0,0.35);
    display: flex;
    justify-content: center;
    align-items: flex-start;
    padding-top: 7px;
    gap: 22px;
    text-decoration: none;
  }
  .cta__label {
    color: var(--cream);
    font-weight: 900;
    font-size: 30px;
    line-height: 1;
    text-shadow: 0 2px 2px rgba(0,0,0,0.35);
  }
  .cta__arrow { width: 110px; height: 30px; }

  .mascot {
    position: absolute;
    left: 905px;
    top: 4px;
    width: 265px;
    height: 176px;
    border-radius: 50% 50% 20% 20%;
    background: radial-gradient(ellipse at 40% 35%, var(--skin-green), var(--shell-brown) 85%);
    opacity: 0.85;
  }
</style>
</head>
<body>
  <div class="banner">
    <div class="banner__rays"></div>

    <h1 class="headline">NEED A MORTGAGE BROKER?</h1>
    <p class="subline">Search now on Australia’s largest directory</p>

    <a class="cta" href="#">
      <svg class="cta__arrow" viewBox="0 0 110 30" aria-hidden="true">
        <line x1="4" y1="15" x2="100" y2="15" stroke="#fff" stroke-width="3.5" stroke-linecap="round"/>
        <polyline points="88,5 102,15 88,25" fill="none" stroke="#fff" stroke-width="3.5" stroke-linecap="round" stroke-linejoin="round"/>
      </svg>
      <span class="cta__label">CLICK HERE</span>
      <svg class="cta__arrow" viewBox="0 0 110 30" aria-hidden="true">
        <line x1="10" y1="15" x2="106" y2="15" stroke="#fff" stroke-width="3.5" stroke-linecap="round"/>
        <polyline points="22,5 8,15 22,25" fill="none" stroke="#fff" stroke-width="3.5" stroke-linecap="round" stroke-linejoin="round"/>
      </svg>
    </a>

    <div class="mascot" role="img" aria-label="Cartoon turtle mascot holding a small house with a red roof"></div>
  </div>
</body>
</html>
```